Quarrybend Marble & Tile Needs a Business Card

Attached you will find your logo, my photo and design guidelines for a new business card. The final design will need two separate files to create an embossed card. The cards will be printed by www.plinkprint.com (Instructions below)
Format is the Plink SQUARE card
Quarrybend Marble And Tile is a brick and mortar, retail stone and tile shop.
One the front:
Quarrybend Marble And Tile
Dorian Fesslock
Owner
24807 Hollis Verdant Blvd
Suite P & R
Charlotte, NC 28193
Cell: 704-583-7142
Web: www.QuarrybendMarbleAndTile.com
(Make each word of the domain a different or alternating color)
On the back;
Something that shows beautiful colorful tile
Follow the design guide closely please. For more information see this page that describes creating the spot gloss file: https://www.plinkprint.com/us/business-cards/design-guidelines-spot-gloss
The logo is what we would like to have raised spot glossed.
Format is the Plink SQUARE card. See attahced guidlines.

```html
<!DOCTYPE html>
<html lang="en">
<head>
<meta charset="utf-8">
<title>Quarrybend Marble &amp; Tile — Business Card</title>
<link rel="stylesheet" href="https://fonts.googleapis.com/css2?family=Cinzel:wght@500&family=Libre+Caslon+Text&family=Montserrat:wght@400;500&display=swap">
<style>
  :root {
    --backdrop: #77787b;
    --slate: #263644;
    --slate-raised: #3b5365;
    --paper: #ffffff;
    --ink: #1f2a33;
    --rust: #a8401c;
    --gold: #c98a2a;
    --olive: #5f6148;
    --photo-dark: #3a3c40;
    --photo-mid: #7a6a5e;
  }
  * { margin: 0; padding: 0; box-sizing: border-box; }
  html, body { width: 900px; height: 1200px; overflow: hidden; }
  body { background: var(--backdrop); position: relative; font-family: "Montserrat", sans-serif; }

  .card { position: absolute; left: 135px; width: 631px; height: 358px; border-radius: 14px; overflow: hidden; }
  .card--back { top: 215px; background: var(--slate); }
  .card--front { top: 628px; background: var(--paper); }

  /* Back: raised wordmark */
  .back-mark { position: absolute; left: 100px; top: 120px; display: flex; align-items: center; gap: 26px; }
  .back-mark__square { width: 74px; height: 74px; background: var(--slate-raised); border-radius: 4px; }
  .wordmark { font-family: "Cinzel", serif; font-weight: 500; color: var(--slate-raised); line-height: 1; }
  .back-mark .wordmark__main { display: block; font-size: 44px; letter-spacing: 6px; }
  .back-mark .wordmark__sub { display: block; font-size: 15px; letter-spacing: 9px; margin-top: 14px; }

  /* Front */
  .portrait-frame { position: absolute; left: 31px; top: 32px; width: 296px; height: 295px; background: var(--rust); }
  .portrait { position: absolute; left: 6px; top: 5px; width: 284px; height: 285px;
    background: radial-gradient(ellipse at 50% 45%, var(--photo-mid) 0%, var(--photo-dark) 70%); }

  .front-logo { position: absolute; right: 31px; top: 34px; display: flex; align-items: center; gap: 12px; }
  .front-logo__square { width: 40px; height: 40px; background: var(--ink); }
  .front-logo .wordmark { color: var(--ink); text-align: right; }
  .front-logo .wordmark__main { display: block; font-size: 23px; letter-spacing: 3px; }
  .front-logo .wordmark__sub { display: block; font-size: 10px; letter-spacing: 5px; margin-top: 6px; }

  .contact { position: absolute; right: 31px; top: 126px; text-align: right; }
  .contact__name { font-family: "Libre Caslon Text", serif; font-size: 24px; color: var(--ink); line-height: 1.1; }
  .contact__role { font-size: 14px; color: var(--rust); margin-top: 2px; }
  .contact__rule { width: 191px; height: 3px; background: var(--rust); margin: 8px 0 12px auto; }
  .contact__line { font-size: 15px; color: var(--ink); line-height: 25px; }
  .contact__phone { font-size: 15px; letter-spacing: 2.5px; color: var(--ink); margin-top: 4px; display: flex; justify-content: flex-end; align-items: center; gap: 3px; }
  .contact__web { font-size: 13px; color: var(--ink); margin-top: 4px; display: flex; justify-content: flex-end; align-items: center; gap: 3px; white-space: nowrap; }
  .web--rust { color: var(--rust); }
  .web--gold { color: var(--gold); }
  .web--olive { color: var(--olive); }
  .icon { width: 14px; height: 14px; fill: none; stroke: var(--gold); stroke-width: 2; }
</style>
</head>
<body>

<section class="card card--back">
  <div class="back-mark">
    <div class="back-mark__square"></div>
    <div class="wordmark">
      <span class="wordmark__main">QUARRYBEND</span>
      <span class="wordmark__sub">MARBLE &amp; TILE</span>
    </div>
  </div>
</section>

<section class="card card--front">
  <div class="portrait-frame">
    <div class="portrait" role="img" aria-label="Portrait photo of the owner in a dark blazer"></div>
  </div>

  <div class="front-logo">
    <div class="front-logo__square"></div>
    <div class="wordmark">
      <span class="wordmark__main">QUARRYBEND</span>
      <span class="wordmark__sub">MARBLE &amp; TILE</span>
    </div>
  </div>

  <div class="contact">
    <div class="contact__name">Dorian Fesslock</div>
    <div class="contact__role">Owner</div>
    <div class="contact__rule"></div>
    <div class="contact__line">24807 Hollis Verdant Blvd</div>
    <div class="contact__line">Suite P &amp; R</div>
    <div class="contact__line">Charlotte, NC 28193</div>
    <div class="contact__phone">704-583-7142
      <svg class="icon" viewBox="0 0 16 16" aria-hidden="true"><path d="M3 2 L6 2 L7 5 L5 6.5 Q7 10 9.5 11 L11 9 L14 10 L14 13 Q8 14 4.5 10 Q2 7 3 2 Z" fill="var(--gold)" stroke="none"/></svg>
    </div>
    <div class="contact__web">
      <span>www.<span class="web--rust">Quarrybend</span><span class="web--gold">Marble</span><span class="web--olive">And</span><span class="web--gold">Tile</span>.com</span>
      <svg class="icon" viewBox="0 0 16 16" aria-hidden="true"><circle cx="8" cy="8" r="6.5"/><ellipse cx="8" cy="8" rx="3" ry="6.5"/><line x1="1.5" y1="8" x2="14.5" y2="8"/></svg>
    </div>
  </div>
</section>

</body>
</html>
```